One page flyer for nonprofit focused IT company

I need a one page flyer (one side of a single 8.5x11 page) with text and graphics. The company logo is already done, and it must appear on the flyer along with other icons and graphics. The final design will be printed on heavy weight glossy paper as a handout and also distributed as a PDF.

The text is provided in an attachment, if it needs to be shortened let me know.

Industry/Entity Type

Information Technology

Requirements
Must have
• some flare (colors, icons or images)
Should not have
• While we work for nonprofits, my company is a FOR PROFIT company.

```html
<!DOCTYPE html>
<html lang="en">
<head>
<meta charset="utf-8">
<title>Northfield Systems Corporation – Nonprofit IT Services Flyer</title>
<link rel="stylesheet" href="https://fonts.googleapis.com/css2?family=Montserrat:wght@600;700;800&family=Arimo:wght@400&display=swap">
<style>
  :root {
    --brand-red: #8e1530;
    --title-gray: #4a4a4c;
    --body-ink: #2b2b2b;
    --footer-gray: #4d4d4f;
    --paper: #ffffff;
    --backdrop: #e9e7e4;
  }
  * { margin: 0; padding: 0; box-sizing: border-box; }
  html, body { width: 1200px; height: 800px; overflow: hidden; }
  body { background: var(--backdrop); font-family: "Arimo", Arial, sans-serif; }

  .flyer {
    position: absolute; left: 306px; top: 20px;
    width: 588px; height: 760px;
    background: var(--paper); overflow: hidden;
  }

  /* Header */
  .brand { position: absolute; left: 44px; top: 78px; display: flex; align-items: center; gap: 7px; }
  .brand-square { width: 12px; height: 12px; background: var(--brand-red); }
  .brand-name { font-family: "Montserrat", sans-serif; font-weight: 700; font-size: 12.5px; color: var(--brand-red); letter-spacing: .2px; }

  .headline { position: absolute; left: 313px; top: 32px; font-family: "Montserrat", sans-serif; font-weight: 800; line-height: .86; }
  .headline .line { display: block; font-size: 26px; color: var(--title-gray); }
  .headline .accent { font-size: 36px; color: var(--brand-red); margin-top: 4px; }

  /* Hero band */
  .hero { position: absolute; left: 0; top: 130px; width: 588px; height: 256px; }
  .hero-image {
    position: absolute; inset: 0;
    background:
      radial-gradient(circle at 27% 60%, rgba(255,226,170,.95) 0, rgba(246,150,50,.75) 14%, rgba(220,110,40,0) 34%),
      radial-gradient(circle at 27% 38%, rgba(140,190,235,.7) 0, rgba(140,190,235,0) 22%),
      linear-gradient(180deg, #4f5a76 0%, #6f6678 30%, #b06a4a 62%, #8a3a22 85%, #5e2a20 100%);
  }
  .hero-copy { position: absolute; left: 313px; top: 28px; width: 245px; color: #fff; }
  .hero-title { font-family: "Montserrat", sans-serif; font-weight: 700; font-size: 15.5px; line-height: 20px; }
  .hero-text { margin-top: 21px; font-size: 9.4px; line-height: 14.5px; }

  /* Section tabs */
  .tab {
    position: absolute; top: 397px; height: 27px; width: 140px;
    background: var(--brand-red); border-top-right-radius: 14px;
    color: #fff; font-family: "Montserrat", sans-serif; font-weight: 800; font-size: 14.5px;
    padding: 5px 0 0 16px;
  }
  .tab-successes { left: 34px; }
  .tab-solutions { left: 293px; padding-left: 13px; }

  .item-title { font-family: "Montserrat", sans-serif; font-weight: 700; font-size: 10px; line-height: 11px; color: var(--brand-red); }
  .item-text { font-size: 7.7px; line-height: 11px; color: var(--body-ink); margin-top: 2px; }

  .successes { position: absolute; left: 32px; top: 436px; width: 236px; }
  .success + .success { margin-top: 11px; }

  .solutions { position: absolute; left: 293px; top: 430px; width: 275px; }
  .solution { display: flex; gap: 8px; align-items: flex-start; }
  .solution + .solution { margin-top: 9px; }
  .solution-icon { flex: 0 0 34px; width: 34px; height: 34px; margin-top: 1px; }
  .solution-body { width: 228px; }

  /* Footer */
  .footer-web {
    position: absolute; left: 0; top: 722px; width: 280px; height: 38px;
    background: var(--brand-red); border-top-right-radius: 16px;
    display: flex; align-items: center; gap: 8px; padding-left: 38px;
    color: #fff; font-family: "Montserrat", sans-serif; font-weight: 700; font-size: 11.5px;
  }
  .footer-contact {
    position: absolute; left: 280px; top: 737px; width: 308px; height: 23px;
    background: var(--footer-gray);
    display: flex; align-items: center; gap: 7px; padding-left: 36px;
    color: #fff; font-family: "Montserrat", sans-serif; font-weight: 600; font-size: 9.5px;
  }
  .footer-contact .gap { width: 4px; }
</style>
</head>
<body>
<main class="flyer">

  <header>
    <div class="brand">
      <span class="brand-square"></span>
      <span class="brand-name">Northfield Systems Corporation</span>
    </div>
    <h1 class="headline">
      <span class="line">50 YEARS</span>
      <span class="line">OF NONPROFIT</span>
      <span class="line accent">IT SERVICES</span>
    </h1>
  </header>

  <section class="hero">
    <div class="hero-image" role="img" aria-label="Photo of a hand at sunset holding a glowing globe wrapped in a network of connected points"></div>
    <div class="hero-copy">
      <h2 class="hero-title">An Efficient and Elegant Approach to IT Solution Implementations</h2>
      <p class="hero-text">Northfield Systems Corporation has been supporting the Information Systems needs of nonprofits for over 50 years. We continually strive to bring the latest technologies and best practices to nonprofits to drive down the cost of IT while implementing systems that drive revenue. Our Agile approach to IT management means that we deliver working systems to every one of our clients every two weeks.</p>
    </div>
  </section>

  <div class="tab tab-successes">SUCCESSES</div>
  <div class="tab tab-solutions">SOLUTIONS</div>

  <section class="successes">
    <article class="success">
      <h3 class="item-title">90% Reduction in Software Development Costs</h3>
      <p class="item-text">Keystone Analytics' National Vehicle Retailers Association needed to update their core product offering; they engaged their in-house IT department who estimated the project would take 3 years at a cost of $3,000,000. NVRA decided to work with Northfield Systems Corporation instead, and the product was released to production in only 9 months at one tenth of the cost, only $300,000</p>
    </article>
    <article class="success">
      <h3 class="item-title">10x Increase in Membership</h3>
      <p class="item-text">Open Pathways Conservancy needed to move to online membership registration and contracted with Northfield Systems Corporation to build a significant online presence and engage potential members. Through compelling online tools and mobile applications Open Pathways has increased membership 10 fold.</p>
    </article>
    <article class="success">
      <h3 class="item-title">20% Reduction in Overhead</h3>
      <p class="item-text">The National Civic Alliance had antiquated systems and processes in place to manage over 500 chapters across the nation. Working with NSC they implemented online tools to allow communication and management between the local chapters and national headquarters. This eliminated much of the overhead of chapter management, reducing HR costs by 20%.</p>
    </article>
  </section>

  <section class="solutions">
    <article class="solution">
      <svg class="solution-icon" viewBox="0 0 34 34" aria-hidden="true">
        <circle cx="17" cy="17" r="17" fill="var(--brand-red)"/>
        <rect x="8" y="10" width="18" height="12" rx="1" fill="none" stroke="#fff" stroke-width="1.3"/>
        <path d="M14 26h6M17 22v4" stroke="#fff" stroke-width="1.3"/>
      </svg>
      <div class="solution-body">
        <h3 class="item-title">Web Applications</h3>
        <p class="item-text">With a focus on non-profit websites and web based applications, NSC helps nonprofits communicate with their members and donors while maximizing online giving and engagement.</p>
      </div>
    </article>
    <article class="solution">
      <svg class="solution-icon" viewBox="0 0 34 34" aria-hidden="true">
        <circle cx="17" cy="17" r="17" fill="var(--brand-red)"/>
        <rect x="11.5" y="8" width="11" height="18" rx="1.5" fill="none" stroke="#fff" stroke-width="1.3"/>
        <circle cx="17" cy="17" r="2.6" fill="none" stroke="#fff" stroke-width="1.2"/>
        <path d="M15.5 23.5h3" stroke="#fff" stroke-width="1.2"/>
      </svg>
      <div class="solution-body">
        <h3 class="item-title">Mobile Applications</h3>
        <p class="item-text">Northfield Systems Corporation implements mobile applications for phones and tablets to provide direct communications with members and donors enabling real-time, two way interaction.</p>
      </div>
    </article>
    <article class="solution">
      <svg class="solution-icon" viewBox="0 0 34 34" aria-hidden="true">
        <circle cx="17" cy="17" r="17" fill="var(--brand-red)"/>
        <circle cx="17" cy="17" r="6" fill="none" stroke="#fff" stroke-width="1.3"/>
        <circle cx="17" cy="17" r="2.2" fill="none" stroke="#fff" stroke-width="1.2"/>
        <path d="M17 8v3M17 23v3M8 17h3M23 17h3M10.6 10.6l2.1 2.1M21.3 21.3l2.1 2.1M10.6 23.4l2.1-2.1M21.3 12.7l2.1-2.1" stroke="#fff" stroke-width="1.3"/>
      </svg>
      <div class="solution-body">
        <h3 class="item-title">Systems Integration</h3>
        <p class="item-text">Every nonprofit's IT applications are scattered and disconnected. Northfield Systems Corporation has decades of experience integrating these applications into a single cohesive system.</p>
      </div>
    </article>
    <article class="solution">
      <svg class="solution-icon" viewBox="0 0 34 34" aria-hidden="true">
        <circle cx="17" cy="17" r="17" fill="var(--brand-red)"/>
        <path d="M9 25h16" stroke="#fff" stroke-width="1.3"/>
        <rect x="10.5" y="18" width="3" height="6" fill="#fff"/>
        <rect x="15.5" y="14" width="3" height="10" fill="#fff"/>
        <rect x="20.5" y="10" width="3" height="14" fill="#fff"/>
      </svg>
      <div class="solution-body">
        <h3 class="item-title">Business Intelligence and Reporting</h3>
        <p class="item-text">Northfield Systems Corporation can wrestle all of an organization's data into simple executive dashboards and reports.</p>
      </div>
    </article>
    <article class="solution">
      <svg class="solution-icon" viewBox="0 0 34 34" aria-hidden="true">
        <circle cx="17" cy="17" r="17" fill="var(--brand-red)"/>
        <path d="M11 23a4 4 0 0 1 0-8 6 6 0 0 1 11.5-1.5A4.8 4.8 0 0 1 23 23z" fill="none" stroke="#fff" stroke-width="1.3"/>
      </svg>
      <div class="solution-body">
        <h3 class="item-title">Cloud Migration</h3>
        <p class="item-text">Reduce IT costs by migrating to the latest cloud solutions.</p>
      </div>
    </article>
    <article class="solution">
      <svg class="solution-icon" viewBox="0 0 34 34" aria-hidden="true">
        <circle cx="17" cy="17" r="17" fill="var(--brand-red)"/>
        <ellipse cx="17" cy="11" rx="6.5" ry="2.3" fill="none" stroke="#fff" stroke-width="1.3"/>
        <path d="M10.5 11v12c0 1.3 2.9 2.3 6.5 2.3s6.5-1 6.5-2.3V11M10.5 17c0 1.3 2.9 2.3 6.5 2.3s6.5-1 6.5-2.3" fill="none" stroke="#fff" stroke-width="1.3"/>
      </svg>
      <div class="solution-body">
        <h3 class="item-title">Member Donor Database</h3>
        <p class="item-text">Northfield Systems Corporation's GiveLedger Member / Donor CRM system is fully customized for each client meeting the unique needs of your organization.</p>
      </div>
    </article>
  </section>

  <footer>
    <div class="footer-web">
      <svg width="15" height="15" viewBox="0 0 16 16" aria-hidden="true">
        <circle cx="8" cy="8" r="7" fill="none" stroke="#fff" stroke-width="1.3"/>
        <ellipse cx="8" cy="8" rx="3" ry="7" fill="none" stroke="#fff" stroke-width="1.1"/>
        <path d="M1 8h14" stroke="#fff" stroke-width="1.1"/>
      </svg>
      <span>www.northfieldsystems.com</span>
    </div>
    <div class="footer-contact">
      <svg width="11" height="11" viewBox="0 0 16 16" aria-hidden="true">
        <path d="M3 1.5l3 3-1.8 1.8a9 9 0 0 0 5.5 5.5L11.5 10l3 3-2 2C6 14.5 1.5 10 1 3.5z" fill="none" stroke="#fff" stroke-width="1.4" stroke-linejoin="round"/>
      </svg>
      <span>010 48 27 90 13</span>
      <span class="gap"></span>
      <svg width="11" height="9" viewBox="0 0 16 12" aria-hidden="true">
        <rect x="1" y="1" width="14" height="10" fill="none" stroke="#fff" stroke-width="1.4"/>
        <path d="M1 1l7 5 7-5" fill="none" stroke="#fff" stroke-width="1.3"/>
      </svg>
      <span>mail@northfieldsystems.com</span>
    </div>
  </footer>

</main>
</body>
</html>
```